Home Remodeling company needs a business card design

we need a business card design for home remodeling company in hamilton county, indiana USA. we offers a wide range of construction services including whole house renovations, Design and Build Basements and Kitchen and Bathroom Remodeling . we would like to see designs for both site of business card that use the same color of the company logo and also including all information below :
1- Karim Feltous CEO / General Contractor
2- all company contacts Telephone numbers ( 1-888-DULOM-47 ) ( 317-555-0193) email address ( info@dulomhome.com) website ( www.dulomhome.com ) and social media logos (Facebook- twitter- google plus )
3- company logo
4- licensed . insured . bonded

```html
<!DOCTYPE html>
<html lang="en">
<head>
<meta charset="utf-8">
<title>Dulom Home Remodeling – Business Card</title>
<link href="https://fonts.googleapis.com/css2?family=Lato:wght@400;700;900&display=swap" rel="stylesheet">
<style>
  :root {
    --backdrop: #8e8e8e;
    --card: #e8e8ea;
    --ink: #3a3a3c;
    --ink-soft: #5c5c5e;
    --accent: #a8262e;
    --rule: #9a9a9c;
  }
  * { box-sizing: border-box; margin: 0; padding: 0; }
  html, body { width: 1105px; height: 1200px; overflow: hidden; }
  body {
    background: var(--backdrop);
    font-family: "Lato", sans-serif;
    color: var(--ink);
    position: relative;
  }
  .card {
    position: absolute;
    left: 182px;
    width: 746px;
    height: 425px;
    background: var(--card);
  }
  .card--front { top: 119px; }
  .card--back { top: 635px; }

  /* Front */
  .brand { position: absolute; left: 47px; top: 44px; }
  .brand__name {
    font-weight: 900;
    font-size: 58px;
    letter-spacing: 3px;
    line-height: 1;
    color: var(--ink);
  }
  .brand__tagline {
    margin-top: 4px;
    font-size: 19px;
    letter-spacing: 6.2px;
    color: var(--ink-soft);
  }
  .contacts {
    position: absolute;
    left: 50px;
    top: 262px;
    list-style: none;
    font-size: 19px;
    color: var(--ink-soft);
  }
  .contacts li {
    display: flex;
    align-items: center;
    height: 29px;
  }
  .contacts svg {
    width: 17px;
    height: 17px;
    margin-right: 12px;
    fill: var(--ink);
  }
  .person {
    position: absolute;
    right: 44px;
    top: 288px;
    text-align: right;
  }
  .person__name { font-size: 26px; font-weight: 700; color: var(--ink); }
  .person__role { margin-top: 4px; font-size: 20px; color: var(--accent); }

  /* Back */
  .back-mark {
    position: absolute;
    left: 50%;
    top: 128px;
    transform: translateX(-50%);
    display: flex;
    flex-direction: column;
    align-items: center;
  }
  .back-mark__square { width: 90px; height: 90px; background: var(--accent); }
  .back-mark__name {
    margin-top: 14px;
    font-size: 26px;
    font-weight: 900;
    letter-spacing: 3px;
    color: var(--accent);
  }
  .credentials {
    position: absolute;
    left: 0; right: 0;
    top: 318px;
    text-align: center;
    font-size: 20px;
    letter-spacing: 0.5px;
    color: var(--accent);
  }
  .social {
    position: absolute;
    left: 50%;
    top: 362px;
    transform: translateX(-50%);
    display: flex;
    align-items: center;
    gap: 5px;
  }
  .social__rule { width: 62px; height: 1px; background: var(--rule); }
  .social__dot {
    width: 24px; height: 24px;
    border-radius: 50%;
    background: var(--ink);
  }
</style>
</head>
<body>
  <section class="card card--front" aria-label="Business card front">
    <div class="brand">
      <div class="brand__name">DULOM</div>
      <div class="brand__tagline">HOME REMODELING</div>
    </div>

    <ul class="contacts">
      <li>
        <svg viewBox="0 0 24 24" aria-hidden="true"><path d="M6.6 10.8a15.1 15.1 0 0 0 6.6 6.6l2.2-2.2c.3-.3.7-.4 1-.2 1.1.4 2.3.6 3.6.6.6 0 1 .4 1 1V20c0 .6-.4 1-1 1A17 17 0 0 1 3 4c0-.6.4-1 1-1h3.5c.6 0 1 .4 1 1 0 1.3.2 2.5.6 3.6.1.3 0 .7-.2 1z"/></svg>
        1-888-DULOM-47
      </li>
      <li>
        <svg viewBox="0 0 24 24" aria-hidden="true"><path d="M7 1h10a2 2 0 0 1 2 2v18a2 2 0 0 1-2 2H7a2 2 0 0 1-2-2V3a2 2 0 0 1 2-2zm0 3v15h10V4z"/></svg>
        317-555-0193
      </li>
      <li>
        <svg viewBox="0 0 24 24" aria-hidden="true"><path d="M2 5h20v14H2zm2 2v.5l8 5 8-5V7zm0 2.8V17h16V9.8l-8 5z"/></svg>
        info@dulomhome.com
      </li>
      <li>
        <svg viewBox="0 0 24 24" aria-hidden="true"><path d="M12 2a10 10 0 1 0 0 20 10 10 0 0 0 0-20zm-1 17.9A8 8 0 0 1 4.2 10.8L9 15.5v1.5c0 1.1.9 2 2 2zm6.9-2.5A2 2 0 0 0 16 16h-1v-3c0-.6-.4-1-1-1H8v-2h2c.6 0 1-.4 1-1V7h2a2 2 0 0 0 2-2v-.4a8 8 0 0 1 2.9 12.8z"/></svg>
        www.dulomhome.com
      </li>
    </ul>

    <div class="person">
      <div class="person__name">Karim Feltous</div>
      <div class="person__role">CEO / General Contractor</div>
    </div>
  </section>

  <section class="card card--back" aria-label="Business card back">
    <div class="back-mark">
      <div class="back-mark__square"></div>
      <div class="back-mark__name">DULOM</div>
    </div>
    <p class="credentials">LICENSED | INSURED | BONDED</p>
    <div class="social" aria-label="Social media links">
      <span class="social__rule"></span>
      <span class="social__dot"></span>
      <span class="social__dot"></span>
      <span class="social__dot"></span>
      <span class="social__rule"></span>
    </div>
  </section>
</body>
</html>
```